Bramble firearms training and consulting

Business card for a new firearms training company. I train persons on firearms safety, personal protection, shooting tactics and CHL.Im a Prior State trooper. I also served 4 years in IRaq as a Protection contractor with the Dept of State. Real world training for Real world situations. I would like the company name to be, BRAMBLE FIREARMS TRAINING AND CONSULTING. Im native american also. Ive provided pics. Put the name Bramble above the arrowhead but rotate the arrowhead to the right with it pointing right. Then place bramble inside the arrowhead. lets see both.
Industry/Entity Type
Business
Contact Information for Business Card
Christian Chatellier817-240-0488shadowtraining33@gmail.com

```html
<!DOCTYPE html>
<html lang="en">
<head>
<meta charset="utf-8">
<title>Bramble Firearms – Business Card</title>
<link rel="stylesheet" href="https://fonts.googleapis.com/css2?family=Raleway:wght@400;500;700&display=swap">
<style>
  :root {
    --page-bg: #1b1c1e;
    --card-bg: #2e3035;
    --brand-red: #c4262e;
    --text-light: #d4d5d8;
    --text-muted: #b9bbbf;
  }
  * { margin: 0; padding: 0; box-sizing: border-box; }
  html, body {
    width: 1200px;
    height: 900px;
    overflow: hidden;
    background: var(--page-bg);
    font-family: "Raleway", Arial, sans-serif;
  }
  .stage { position: relative; width: 1200px; height: 900px; }
  .card {
    position: absolute;
    left: 331px;
    width: 547px;
    height: 319px;
    border-radius: 20px;
    background: var(--card-bg);
  }
  .card--front { top: 119px; }
  .card--back { top: 486px; }

  .brand-mark {
    position: absolute;
    display: flex;
    align-items: center;
    gap: 12px;
    color: var(--brand-red);
    font-weight: 700;
  }
  .brand-mark__dot {
    width: 26px; height: 26px;
    border-radius: 50%;
    background: var(--brand-red);
    flex: none;
  }
  .card--front .brand-mark {
    left: 52px; top: 140px;
    font-size: 30px;
  }

  .contact { position: absolute; left: 284px; top: 118px; }
  .contact__name {
    color: var(--brand-red);
    font-size: 25px;
    font-weight: 400;
    line-height: 30px;
    white-space: nowrap;
  }
  .contact__role {
    color: var(--text-muted);
    font-size: 16px;
    line-height: 20px;
  }
  .contact__details {
    margin-top: 20px;
    margin-left: 4px;
    color: var(--text-light);
    font-size: 14.5px;
    line-height: 19px;
    list-style: none;
    white-space: nowrap;
  }

  .card--back .brand-mark {
    left: 0; right: 0; top: 101px;
    flex-direction: column;
    gap: 36px;
    text-align: center;
    font-size: 22px;
    line-height: 28px;
    letter-spacing: 0.5px;
  }
  .card--back .brand-mark__dot { width: 40px; height: 40px; }
</style>
</head>
<body>
<main class="stage">
  <section class="card card--front" aria-label="Card front">
    <div class="brand-mark">
      <span class="brand-mark__dot"></span>
      <span class="brand-mark__name">Bramble</span>
    </div>
    <div class="contact">
      <h1 class="contact__name">Dorian Pellwick</h1>
      <p class="contact__role">Managing Director</p>
      <ul class="contact__details">
        <li>bramblecourse58@mailvento.com</li>
        <li>555-317-9062</li>
      </ul>
    </div>
  </section>

  <section class="card card--back" aria-label="Card back">
    <div class="brand-mark">
      <span class="brand-mark__dot"></span>
      <span class="brand-mark__name">BRAMBLE FIREARMS<br>TRAINING AND CONSULTING</span>
    </div>
  </section>
</main>
</body>
</html>
```